Business Card Design

Hi I need a business card designed, we already have the business name logo artwork and would like some concept ideas for the Bus Card layout.
On the back of the card i want to include the products and services that we offer.
We are a Plastics Sheeting manufacture based in Perth Australia.

                                       

We need a BC design for a company called Tarvo Plastics based in Perth Australia.

We supply from DIY to Trade & Industrial  Engineering Markets.

We specialise in:

·         Cut to size panels  (all shapes and sizes)

·         Plastics fabrication & Welding

·         Custom Designs

·         Plastic Repairs

·         PVC Pipe Slotting & PVC Pipe Threading

·         Supplier of all types of engineering plastics and profiles.

Including:           Acrylic / Clarvene

                               Polycarbonate / Dorvil

                               Prismatic Light Diffuser

                               Vantrib

                               HDPE / UHMWPE

                               PVC / PVC Foam

                               Nylon

                               HIPS

```html
<!DOCTYPE html>
<html lang="en">
<head>
<meta charset="utf-8">
<title>Tarvo Plastics – Business Card</title>
<link rel="stylesheet" href="https://fonts.googleapis.com/css2?family=Source+Sans+3:wght@400;600;700&display=swap">
<style>
  :root {
    --navy: #1b2a63;
    --navy-text: #1d2f6f;
    --bullet: #2a7fd0;
    --silver-light: #f1f2f3;
    --silver-mid: #d9dbde;
    --silver-dark: #c4c7cb;
    --grey-text: #555a62;
    --white: #ffffff;
    --backdrop: #e6e7e9;
  }
  * { box-sizing: border-box; margin: 0; padding: 0; }
  html, body { width: 1200px; height: 720px; overflow: hidden; }
  body {
    background: var(--backdrop);
    font-family: "Source Sans 3", "Myriad Pro", sans-serif;
    display: flex;
    align-items: center;
    justify-content: center;
    gap: 40px;
  }
  .card {
    width: 540px;
    height: 310px;
    position: relative;
    overflow: hidden;
    background: linear-gradient(160deg, var(--silver-light) 0%, var(--silver-mid) 45%, var(--silver-light) 70%, var(--silver-dark) 100%);
    box-shadow: 0 4px 14px rgba(0,0,0,.18);
  }

  /* Front */
  .brand {
    position: absolute;
    left: 38px;
    top: 26px;
    display: flex;
    align-items: center;
    gap: 12px;
    color: var(--navy);
    font-weight: 700;
    font-size: 42px;
    letter-spacing: .3px;
  }
  .brand-mark { width: 22px; height: 22px; background: var(--navy); }
  .address {
    position: absolute;
    left: 0; right: 0;
    top: 88px;
    padding-left: 90px;
    text-align: center;
    color: var(--grey-text);
    font-size: 14px;
    line-height: 1.3;
  }
  .contact-band {
    position: absolute;
    left: 0; right: 0; bottom: 0;
    height: 170px;
    background: var(--navy);
    color: var(--white);
    padding: 26px 30px;
  }
  .person { font-size: 19px; font-weight: 700; margin-bottom: 10px; }
  .person .title { font-size: 14px; font-weight: 400; }
  .contact-list { list-style: none; font-size: 14.5px; line-height: 1.6; }
  .contact-list li { display: flex; align-items: center; gap: 6px; }
  .contact-list .pair { gap: 14px; }
  .contact-list span { display: inline-flex; align-items: center; gap: 6px; }
  .icon { width: 13px; height: 13px; fill: var(--white); flex: none; }

  /* Back */
  .card-back {
    padding: 26px 24px 0;
    text-align: center;
    color: var(--navy-text);
  }
  .offer-heading { font-size: 15px; font-weight: 700; line-height: 1.25; }
  .section-title { font-size: 20px; font-weight: 700; margin: 10px 0 4px; }
  .section-title.including { margin-top: 12px; }
  .item-row {
    list-style: none;
    display: flex;
    justify-content: center;
    flex-wrap: wrap;
    gap: 0 14px;
    color: var(--grey-text);
    font-size: 13.5px;
    line-height: 1.45;
  }
  .item-row li::before {
    content: "";
    display: inline-block;
    width: 6px; height: 6px;
    border-radius: 50%;
    background: var(--bullet);
    margin-right: 6px;
    vertical-align: middle;
  }
</style>
</head>
<body>

<section class="card card-front" aria-label="Business card front">
  <div class="brand"><span class="brand-mark"></span>Tarvo Plastics</div>
  <p class="address">Unit 4/18 Merlow Circuit Brenfield WA 6152<br>PO Box 2270 Brenfield DC WA 6981</p>
  <div class="contact-band">
    <p class="person">Your Name, <span class="title">Title</span></p>
    <ul class="contact-list">
      <li>
        <svg class="icon" viewBox="0 0 16 16"><path d="M3 1l3 3-2 2c1 2 3 4 5 5l2-2 3 3-2 3C7 15 1 9 1 3z"/></svg>
        08 9471 3350
      </li>
      <li class="pair">
        <span>
          <svg class="icon" viewBox="0 0 16 16"><rect x="4" y="1" width="8" height="14" rx="1.5"/><rect x="6" y="3" width="4" height="7" fill="#1b2a63"/></svg>
          0400 555 018
        </span>
        <span>
          <svg class="icon" viewBox="0 0 16 16"><rect x="1" y="6" width="14" height="8" rx="1"/><rect x="4" y="2" width="8" height="5"/></svg>
          08 9471 3360
        </span>
      </li>
      <li>
        <svg class="icon" viewBox="0 0 16 16"><rect x="1" y="3" width="14" height="10" rx="1"/><path d="M1.5 4l6.5 5 6.5-5" fill="none" stroke="#1b2a63" stroke-width="1.4"/></svg>
        sales@tarvoplastics.com.au
      </li>
    </ul>
  </div>
</section>

<section class="card card-back" aria-label="Business card back">
  <h2 class="offer-heading">The Products And Services That We Offer<br>Are Supplied From Diy To Trade &amp; Industrial Engineering Markets</h2>
  <h3 class="section-title">We specialise in:</h3>
  <ul class="item-row"><li>Cut to size panels (all shapes and sizes)</li><li>Custom Designs</li></ul>
  <ul class="item-row"><li>Plastics fabrication &amp; Welding</li><li>PVC Pipe Threading</li></ul>
  <ul class="item-row"><li>Plastic Repairs</li><li>PVC Pipe Slotting</li></ul>
  <ul class="item-row"><li>Supplier of all types of engineering plastics and profiles</li></ul>
  <h3 class="section-title including">Including:</h3>
  <ul class="item-row"><li>Acrylic / Clarvene</li><li>Polycarbonate / Dorvil</li></ul>
  <ul class="item-row"><li>Prismatic Light Diffuser</li><li>Vantrib</li><li>HDPE / UHMWPE</li></ul>
  <ul class="item-row"><li>PVC / PVC Foam</li><li>Nylon</li><li>HIPS</li></ul>
</section>

</body>
</html>
```